Business Cards + Flyer + Letterhead for Care Recruitment Agency

We are a recruitment agency for the health & care sector. We need designs made for business cards, A5 double-sided flyer, and a letterhead template.

Our branding message is professionalism, care, compassion, expertise. We are experts in recruitment for the care & health industry.

Our logo source files and colours are here - https://www.filevault-example.net/sh/q8rn27lpzw4xkc/BBRtLm3QPW92dKfYhNvZceLmo?dl=0

For the business card, I have attached an example we like. We want a vertical business card design, something very similar to the example given. The design should match our logo in terms of brand colors. On one side should be our logo, our website (www.holbrookelune.co.uk) and Care Recruitment Specialists written somewhere visible that fits, between our logo and the website at the bottom. On the other side should be our details.

Details on the front:

Logo with slogan
Care Recruitment Specialists
www.holbrookelune.co.uk

Details on the back:

Dominic Argyros
Managing Director

Radley Court, 40-48 Pellow St, Birmingham, B7 9QX
07612 495137
dominic@holbrookelune.co.uk
www.holbrookelune.co.uk

Nadia Holbrooke
Business Development Director

07731 284956
nadia@holbrookelune.co.uk
www.holbrookelune.co.uk

For the A5 flyer, I have attached some pictures we've used for the website, which could be used for the flyer as well. To get a better idea of our branding, please visit our website - https://holbrookelune.co.uk/

The text for the flyer is also attached.

Finally, the letterhead template should be a docx template with our logo and our identifiable branding (the same shapes and matching colours you will come up with for the business cards and flyer).

```html
<!DOCTYPE html>
<html lang="en">
<head>
<meta charset="utf-8">
<title>Holbrooke Lune – Stationery Set</title>
<link rel="stylesheet" href="https://fonts.googleapis.com/css2?family=Lato:wght@400&family=Poppins:wght@400;600;700;800&display=swap">
<style>
  :root {
    --cyan: #00cbff;
    --blue: #0a6cff;
    --navy: #102a5c;
    --ink: #1b1b1e;
    --paper: #ffffff;
    --stage: #cbcbcd;
    --text: #1d1d1f;
    --brand-gradient: linear-gradient(135deg, var(--cyan) 0%, var(--blue) 50%, var(--navy) 100%);
  }
  * { margin: 0; padding: 0; box-sizing: border-box; }
  html, body { width: 1200px; height: 906px; overflow: hidden; }
  body { position: relative; background: var(--stage); font-family: "Poppins", sans-serif; }

  .stage-accent { position: absolute; inset: 0; width: 1200px; height: 906px; }

  .sheet { position: absolute; background: var(--paper); box-shadow: 8px 10px 14px rgba(0,0,0,.18); overflow: hidden; }

  .top-stripes { position: absolute; top: 0; left: 0; right: 0; display: flex; justify-content: space-between; }
  .top-stripes span { display: block; height: 100%; }
  .top-stripes .c { background: var(--cyan); }
  .top-stripes .n { background: var(--navy); }

  /* ---------- letterhead ---------- */
  .letterhead { left: 50px; top: 49px; width: 568px; height: 803px; font-family: "Lato", sans-serif; color: var(--text); }
  .letterhead .top-stripes { height: 8px; }
  .letterhead .top-stripes .c:first-child { width: 183px; }
  .letterhead .top-stripes .n { width: 186px; }
  .letterhead .top-stripes .c:last-child { width: 185px; }

  .brand-lockup { position: absolute; top: 56px; left: 0; right: 0; display: flex; justify-content: center; align-items: center; gap: 10px; }
  .brand-mark { width: 22px; height: 22px; background: var(--blue); }
  .brand-name { font-family: "Poppins", sans-serif; font-weight: 700; font-size: 24px; letter-spacing: 2.5px; color: var(--navy); }

  .lh-field { position: absolute; font-size: 12.4px; line-height: 14px; }
  .lh-name { left: 53px; top: 165px; }
  .lh-address { left: 53px; top: 194px; }
  .lh-date { right: 53px; top: 194px; }

  .lh-body { position: absolute; left: 53px; width: 462px; top: 226px; font-size: 12.4px; line-height: 14.7px; text-align: justify; }
  .lh-body p + p { margin-top: 14.7px; }

  .lh-regards { left: 53px; top: 556px; }
  .signature-area { position: absolute; left: 36px; top: 580px; width: 131px; height: 52px; background: linear-gradient(90deg, #f1f1f3, #e6e6ea); border-radius: 4px; }
  .lh-sign-name { left: 53px; top: 644px; }
  .lh-sign-role { left: 53px; top: 659px; }

  .lh-footer { position: absolute; left: 0; bottom: 0; width: 568px; height: 80px; background: var(--ink); }
  .footer-block { position: absolute; top: 0; bottom: 0; background: var(--brand-gradient); }
  .footer-block.left { left: 0; width: 118px; }
  .footer-block.right { right: 0; width: 92px; background: linear-gradient(315deg, var(--cyan) 0%, var(--blue) 50%, var(--navy) 100%); }
  .lh-contact { position: absolute; display: flex; align-items: center; gap: 5px; font-family: "Poppins", sans-serif; font-size: 9.5px; color: #fff; }
  .lh-contact svg { width: 12px; height: 12px; flex: none; }

  /* ---------- business cards ---------- */
  .card { width: 213px; height: 373px; }
  .card .top-stripes { height: 4px; }
  .card .top-stripes .c:first-child { width: 68px; }
  .card .top-stripes .n { width: 72px; }
  .card .top-stripes .c:last-child { width: 67px; }

  .card-art { position: absolute; left: 0; right: 0; background: var(--brand-gradient); }
  .card-base { position: absolute; left: 0; right: 0; bottom: 0; background: var(--ink); }

  .card-front { left: 675px; top: 49px; }
  .card-front .card-art { top: 196px; height: 141px; }
  .card-front .card-base { height: 36px; }
  .card-back-a { left: 675px; top: 477px; }
  .card-back-b { left: 933px; top: 477px; }
  .card-back-a .card-art, .card-back-b .card-art { top: 100px; height: 146px; }
  .card-back-a .card-base, .card-back-b .card-base { height: 127px; }

  .front-lockup { position: absolute; top: 112px; left: 0; right: 0; text-align: center; }
  .front-lockup .brand-name { font-size: 17px; letter-spacing: 1.4px; line-height: 20px; }
  .front-tagline { font-size: 7.6px; letter-spacing: 1.6px; color: var(--navy); font-weight: 400; margin-top: 1px; }
  .front-web { position: absolute; left: 0; right: 0; top: 351px; text-align: center; color: #fff; font-size: 7.5px; letter-spacing: 2.6px; }

  .person { position: absolute; top: 44px; left: 0; right: 0; text-align: center; }
  .person-name { font-weight: 800; font-size: 17.5px; color: var(--blue); letter-spacing: .2px; line-height: 20px; }
  .person-role { font-size: 6.8px; color: #2a2a2e; letter-spacing: .3px; }

  .card-details { position: absolute; left: 20px; top: 267px; list-style: none; color: #fff; font-size: 9.4px; line-height: 11px; }
  .card-details li { display: flex; align-items: flex-start; gap: 8px; margin-bottom: 9px; }
  .card-details svg { width: 14px; height: 14px; flex: none; margin-top: -1px; }
</style>
</head>
<body>

<svg width="0" height="0" style="position:absolute" aria-hidden="true">
  <defs>
    <symbol id="icon-phone" viewBox="0 0 24 24">
      <circle cx="12" cy="12" r="10.5" fill="none" stroke="#0a6cff" stroke-width="1.8"/>
      <path d="M8.6 7.2l1.7-.4 1 2.4-1.2.9a7 7 0 0 0 3.8 3.8l.9-1.2 2.4 1-.4 1.7c-4.6.4-8.6-3.6-8.2-8.2z" fill="none" stroke="#0a6cff" stroke-width="1.4" stroke-linejoin="round"/>
    </symbol>
    <symbol id="icon-pin" viewBox="0 0 24 24">
      <circle cx="12" cy="12" r="10.5" fill="none" stroke="#0a6cff" stroke-width="1.8"/>
      <path d="M12 18.2s-4.2-4.4-4.2-7.4a4.2 4.2 0 0 1 8.4 0c0 3-4.2 7.4-4.2 7.4z" fill="none" stroke="#0a6cff" stroke-width="1.5"/>
      <circle cx="12" cy="10.8" r="1.5" fill="#0a6cff"/>
    </symbol>
    <symbol id="icon-mail" viewBox="0 0 24 24">
      <circle cx="12" cy="12" r="10.5" fill="none" stroke="#0a6cff" stroke-width="1.8"/>
      <rect x="7" y="8.5" width="10" height="7" rx="1" fill="#0a6cff"/>
      <path d="M7.3 9l4.7 3.6L16.7 9" fill="none" stroke="#fff" stroke-width="1"/>
    </symbol>
    <symbol id="icon-web" viewBox="0 0 24 24">
      <circle cx="12" cy="12" r="10.5" fill="none" stroke="#0a6cff" stroke-width="1.8"/>
      <circle cx="12" cy="12" r="5.5" fill="none" stroke="#0a6cff" stroke-width="1.2"/>
      <ellipse cx="12" cy="12" rx="2.3" ry="5.5" fill="none" stroke="#0a6cff" stroke-width="1.1"/>
      <path d="M6.5 12h11M7.3 9.2h9.4M7.3 14.8h9.4" stroke="#0a6cff" stroke-width="1.1"/>
    </symbol>
    <symbol id="icon-phone-white" viewBox="0 0 24 24">
      <circle cx="12" cy="12" r="11" fill="#fff"/>
      <rect x="8.5" y="5.5" width="7" height="13" rx="1.4" fill="none" stroke="#0a6cff" stroke-width="1.6"/>
    </symbol>
    <symbol id="icon-pin-white" viewBox="0 0 24 24">
      <circle cx="12" cy="12" r="11" fill="#fff"/>
      <path d="M12 18.5s-4.3-4.5-4.3-7.6a4.3 4.3 0 0 1 8.6 0c0 3.1-4.3 7.6-4.3 7.6z" fill="none" stroke="#0a6cff" stroke-width="1.6"/>
    </symbol>
    <symbol id="icon-mail-white" viewBox="0 0 24 24">
      <circle cx="12" cy="12" r="11" fill="#fff"/>
      <rect x="6.5" y="8" width="11" height="8" rx="1" fill="#0a6cff"/>
      <path d="M6.8 8.5l5.2 4 5.2-4" fill="none" stroke="#fff" stroke-width="1"/>
    </symbol>
    <symbol id="icon-web-white" viewBox="0 0 24 24">
      <circle cx="12" cy="12" r="11" fill="#fff"/>
      <circle cx="12" cy="12" r="5.8" fill="none" stroke="#0a6cff" stroke-width="1.3"/>
      <ellipse cx="12" cy="12" rx="2.4" ry="5.8" fill="none" stroke="#0a6cff" stroke-width="1.1"/>
      <path d="M6.2 12h11.6" stroke="#0a6cff" stroke-width="1.1"/>
    </symbol>
  </defs>
</svg>

<svg class="stage-accent" viewBox="0 0 1200 906" aria-hidden="true">
  <path d="M288,906 L1200,483 L1200,906 Z" fill="#00cbff"/>
</svg>

<!-- Letterhead -->
<article class="sheet letterhead">
  <div class="top-stripes"><span class="c"></span><span class="n"></span><span class="c"></span></div>

  <header class="brand-lockup">
    <span class="brand-mark"></span>
    <span class="brand-name">HOLBROOKE LUNE</span>
  </header>

  <div class="lh-field lh-name">Your Name Here</div>
  <div class="lh-field lh-address">Address</div>
  <div class="lh-field lh-date">Date : 17th September, 2020</div>

  <div class="lh-body">
    <p>Lorem Ipsum is simply dummy text of the printing and typesetting industry. Lorem Ipsum has been the industry's standard dummy text ever since the 1500s, when an unknown printer took a galley of type and scrambled it to make a type specimen book. It has survived not only five centuries, but also the leap into electronic typesetting, remaining essentially unchanged. It was popularised in the 1960s with the release of Pressmark sheets containing Lorem Ipsum passages, and more recently with desktop publishing software like Quillset Layout including versions of Lorem Ipsum.</p>
    <p>Lorem Ipsum is simply dummy text of the printing and typesetting industry. Lorem Ipsum has been the industry's standard dummy text ever since the 1500s, when an unknown printer took a galley of type and scrambled it to make a type specimen book. but also the leap into electronic typesetting, remaining essentially unchanged. It was popularised in the 1960s with the release of Pressmark sheets containing Lorem Ipsum passages, and more recently with desktop publishing software like Quillset Layout including versions of Lorem Ipsum.</p>
    <p>It has survived not only five centuries, but also the leap into electronic typesetting, remaining essentially unchanged. It was popularised in the 1960s with the release of Pressmark sheets containing Lorem Ipsum passages, and more recently with desktop publishing software like Quillset Layout including versions of Lorem Ipsum.</p>
  </div>

  <div class="lh-field lh-regards">Regards,</div>
  <div class="signature-area" role="img" aria-label="Handwritten signature"></div>
  <div class="lh-field lh-sign-name">Your Name Here</div>
  <div class="lh-field lh-sign-role">Designation Here</div>

  <footer class="lh-footer">
    <div class="footer-block left" role="img" aria-label="Brand graphic in cyan, blue and navy"></div>
    <div class="footer-block right" role="img" aria-label="Brand graphic in cyan, blue and navy"></div>
  </footer>
  <div class="lh-contact" style="left:150px; top:750px;"><svg><use href="#icon-phone-white"/></svg>12345 54321</div>
  <div class="lh-contact" style="left:150px; top:770px;"><svg><use href="#icon-pin-white"/></svg>lorem ipsum dolor sit amet</div>
  <div class="lh-contact" style="left:307px; top:748px;"><svg><use href="#icon-mail-white"/></svg>loremipsum@inboxmail.net</div>
  <div class="lh-contact" style="left:307px; top:768px;"><svg><use href="#icon-web-white"/></svg>www.holbrookelune.co.uk</div>
</article>

<!-- Card front -->
<article class="sheet card card-front">
  <div class="top-stripes"><span class="c"></span><span class="n"></span><span class="c"></span></div>
  <header class="front-lockup">
    <div class="brand-name">HOLBROOKE LUNE</div>
    <div class="front-tagline">CARE RECRUITMENT SPECIALISTS</div>
  </header>
  <div class="card-art" role="img" aria-label="Brand graphic in cyan, blue and navy"></div>
  <div class="card-base"></div>
  <div class="front-web">WWW.HOLBROOKELUNE.CO.UK</div>
</article>

<!-- Card back: Managing Director -->
<article class="sheet card card-back-a">
  <div class="top-stripes"><span class="c"></span><span class="n"></span><span class="c"></span></div>
  <header class="person">
    <div class="person-name">DOMINIC ARGYROS</div>
    <div class="person-role">MANAGING DIRECTOR</div>
  </header>
  <div class="card-art" role="img" aria-label="Brand graphic in cyan, blue and navy"></div>
  <div class="card-base"></div>
  <ul class="card-details">
    <li><svg><use href="#icon-phone"/></svg><span>07612 495137</span></li>
    <li><svg><use href="#icon-pin"/></svg><span>Radley Court, 40-48 Pellow St,<br>Birmingham, B7 9QX</span></li>
    <li><svg><use href="#icon-mail"/></svg><span>dominic@holbrookelune.co.uk</span></li>
    <li><svg><use href="#icon-web"/></svg><span>www.holbrookelune.co.uk</span></li>
  </ul>
</article>

<!-- Card back: Business Development Director -->
<article class="sheet card card-back-b">
  <div class="top-stripes"><span class="c"></span><span class="n"></span><span class="c"></span></div>
  <header class="person">
    <div class="person-name">NADIA HOLBROOKE</div>
    <div class="person-role">BUSINESS DEVELOPMENT DIRECTOR</div>
  </header>
  <div class="card-art" role="img" aria-label="Brand graphic in cyan, blue and navy"></div>
  <div class="card-base"></div>
  <ul class="card-details">
    <li><svg><use href="#icon-phone"/></svg><span>07731 284956</span></li>
    <li><svg><use href="#icon-pin"/></svg><span>Radley Court, 40-48 Pellow St,<br>Birmingham, B7 9QX</span></li>
    <li><svg><use href="#icon-mail"/></svg><span>nadia@holbrookelune.co.uk</span></li>
    <li><svg><use href="#icon-web"/></svg><span>www.holbrookelune.co.uk</span></li>
  </ul>
</article>

</body>
</html>
```